New Zealand Marlborough Sauvignon Blanc wine packaging design

We need packaging design for our new wine brand, Dunmore Vale. The wine is a New Zealand Marlborough Sauvignon Blanc. We would like the packaging will portray elegance and style with an understated label. We are looking for a label that portrays the elegance of the French Riviera. The label should be round or pill shaped.
Updates

Industry/Entity Type

Wine

Font styles to use
Serif
Sans Serif

Requirements
Must have
• The words in order of importance: Dunmore Vale, Sauvignon Blanc, Marlborough, New Zealand. It should be fit to the bottle posted in the links
Nice to have
• a pill shape or circular shape
Should not have
• Illustrations of wine bottles, wine glasses, or grapes

```html
<!DOCTYPE html>
<html lang="en">
<head>
<meta charset="utf-8">
<title>Dunmore Vale — Sauvignon Blanc Label</title>
<link rel="stylesheet" href="https://fonts.googleapis.com/css2?family=Great+Vibes&family=Oswald:wght@300;400&display=swap">
<style>
  :root {
    --page: #ffffff;
    --frame-grey: #a3a8aa;
    --line-grey: #9c9c9c;
    --text-grey: #8f9496;
    --script-grey: #a6abad;
    --citrus: #d9d40c;
    --hill-lime: #c9cf3a;
    --hill-sage: #dfe3c4;
  }
  html, body {
    margin: 0;
    padding: 0;
    width: 1200px;
    height: 675px;
    overflow: hidden;
    background: var(--page);
  }
  .canvas {
    width: 1200px;
    height: 675px;
    display: flex;
    align-items: center;
    justify-content: center;
  }
  .wine-label {
    width: 366px;
    height: 580px;
    display: block;
  }
  .label-outer { fill: var(--page); stroke: var(--frame-grey); stroke-width: 7; }
  .label-inner { fill: none; stroke: var(--line-grey); stroke-width: 1.5; }
  .name-banner { fill: var(--page); stroke: var(--line-grey); stroke-width: 1.5; }
  .rule { stroke: var(--line-grey); stroke-width: 2; }
  .brand-mark {
    font-family: 'Oswald', sans-serif;
    font-weight: 400;
    font-size: 17px;
    letter-spacing: 3px;
    fill: var(--citrus);
  }
  .brand-script {
    font-family: 'Great Vibes', cursive;
    font-size: 118px;
    fill: var(--script-grey);
  }
  .varietal {
    font-family: 'Oswald', sans-serif;
    font-weight: 300;
    font-size: 34px;
    fill: var(--text-grey);
  }
  .region {
    font-family: 'Oswald', sans-serif;
    font-weight: 300;
    font-size: 19px;
    fill: var(--text-grey);
  }
</style>
</head>
<body>
<main class="canvas">
  <svg class="wine-label" viewBox="258 168 736 1166" xmlns="http://www.w3.org/2000/svg" aria-label="Dunmore Vale Sauvignon Blanc wine label">
    <defs>
      <radialGradient id="hillsGlow" cx="0.5" cy="0.6" r="0.55">
        <stop offset="0" stop-color="var(--hill-lime)"/>
        <stop offset="0.5" stop-color="var(--hill-sage)"/>
        <stop offset="1" stop-color="var(--page)" stop-opacity="0"/>
      </radialGradient>
    </defs>

    <rect class="label-outer" x="268" y="177" width="716" height="1148" rx="358"/>
    <rect class="label-inner" x="365" y="273" width="522" height="952" rx="261"/>

    <text class="brand-mark" x="626" y="418" text-anchor="middle">DUNMORE VALE</text>

    <g role="img" aria-label="Soft watercolour hills of the Marlborough valley in lime and sage tones">
      <ellipse cx="630" cy="505" rx="195" ry="80" fill="url(#hillsGlow)"/>
    </g>

    <rect class="name-banner" x="296" y="619" width="660" height="211" rx="12"/>
    <text class="brand-script" x="626" y="765" text-anchor="middle" textLength="580" lengthAdjust="spacingAndGlyphs">Dunmore Vale</text>

    <line class="rule" x1="407" y1="833" x2="845" y2="833"/>
    <text class="varietal" x="626" y="878" text-anchor="middle" textLength="425" lengthAdjust="spacing">SAUVIGNON BLANC</text>
    <line class="rule" x1="407" y1="897" x2="845" y2="897"/>

    <text class="region" x="626" y="1050" text-anchor="middle" textLength="350" lengthAdjust="spacing">NEW ZEALAND MARLBOROUGH</text>
  </svg>
</main>
</body>
</html>
```